Bramwell Crest Electric van design

Looking to design a wrap for a 2021 varenta cargolux high roof using orange black and dark grey colors like in the logo

```html
<!DOCTYPE html>
<html lang="en">
<head>
<meta charset="utf-8">
<title>Bramwell Crest Electric – varenta cargolux wrap</title>
<link rel="stylesheet" href="https://fonts.googleapis.com/css2?family=Montserrat:wght@800&family=Barlow+Condensed:wght@600&display=swap">
<style>
  :root {
    --wrap-orange: #d9694a;
    --wrap-charcoal: #3e3e41;
    --wrap-white: #ededed;
    --trim-black: #242426;
    --tyre: #1c1c1d;
    --hub: #a9abad;
    --glass: #2c3330;
    --lamp-red: #b8212b;
    --canvas-bg: #e6e6e4;
  }
  html, body {
    margin: 0;
    padding: 0;
    overflow: hidden;
  }
  body {
    width: 686px;
    height: 1200px;
    background: var(--canvas-bg);
  }
  .wrap-sheet {
    width: 686px;
    height: 1200px;
    display: flex;
    flex-direction: column;
    align-items: center;
    justify-content: space-evenly;
  }
  .van-view { display: block; }
  .wordmark {
    font-family: "Montserrat", sans-serif;
    font-weight: 800;
    fill: var(--wrap-white);
  }
  .contact {
    font-family: "Barlow Condensed", sans-serif;
    font-weight: 600;
    fill: var(--wrap-white);
  }
  .contact.on-roof { fill: var(--wrap-orange); }
</style>
</head>
<body>
<main class="wrap-sheet">

  <!-- Side elevation -->
  <svg class="van-view van-side" width="686" height="360" viewBox="0 0 686 360" aria-label="Van side wrap layout">
    <defs>
      <clipPath id="side-body-clip">
        <path d="M22 296 L22 62 Q22 40 46 40 L500 40 Q528 40 548 66 L618 150 Q664 170 668 214 L668 296 Z"/>
      </clipPath>
    </defs>
    <g class="side-body">
      <path fill="var(--wrap-charcoal)" d="M22 296 L22 62 Q22 40 46 40 L500 40 Q528 40 548 66 L618 150 Q664 170 668 214 L668 296 Z"/>
      <g clip-path="url(#side-body-clip)">
        <polygon class="roof-panel" fill="var(--wrap-white)" points="250,30 560,30 560,140 440,112 300,84"/>
        <path class="swoosh-band" fill="var(--wrap-orange)" d="M22 250 L190 30 L250 30 Q320 130 290 230 Q270 280 250 320 L22 320 Z"/>
        <path class="swoosh-line" fill="none" stroke="var(--wrap-white)" stroke-width="5" d="M262 30 Q336 132 302 236 Q286 282 266 320"/>
        <rect class="rocker-trim" x="22" y="262" width="646" height="40" fill="var(--trim-black)" opacity="0.55"/>
      </g>
      <path class="cab-window" fill="var(--glass)" d="M482 84 L530 84 Q540 84 548 94 L592 150 L482 150 Z"/>
      <rect class="tail-lamp" x="22" y="140" width="10" height="46" fill="var(--lamp-red)"/>
      <line x1="470" y1="60" x2="470" y2="290" stroke="var(--trim-black)" stroke-width="1.5" opacity="0.6"/>
      <line x1="330" y1="44" x2="330" y2="290" stroke="var(--trim-black)" stroke-width="1.5" opacity="0.4"/>
    </g>

    <text class="contact on-roof site-url" x="298" y="72" font-size="13" transform="rotate(6 298 72)">www.bramwellcrestelectric.com</text>
    <g transform="rotate(7 320 140)">
      <text class="wordmark" x="212" y="124" font-size="38">Bramwell</text>
      <text class="wordmark" x="208" y="160" font-size="25">Crest Electric</text>
    </g>
    <text class="contact phone" x="480" y="182" font-size="22" transform="rotate(4 480 182)">555.014.2290</text>

    <g class="wheels">
      <circle cx="140" cy="300" r="38" fill="var(--tyre)"/>
      <circle cx="140" cy="300" r="20" fill="var(--hub)"/>
      <circle cx="560" cy="300" r="38" fill="var(--tyre)"/>
      <circle cx="560" cy="300" r="20" fill="var(--hub)"/>
    </g>
  </svg>

  <!-- Rear elevation -->
  <svg class="van-view van-rear" width="686" height="800" viewBox="0 0 686 800" aria-label="Van rear wrap layout">
    <defs>
      <clipPath id="rear-body-clip">
        <path d="M190 40 L496 40 Q520 40 524 66 L540 700 L146 700 L162 66 Q166 40 190 40 Z"/>
      </clipPath>
    </defs>
    <g class="rear-body">
      <path fill="var(--wrap-charcoal)" d="M190 40 L496 40 Q520 40 524 66 L540 700 L146 700 L162 66 Q166 40 190 40 Z"/>
      <g clip-path="url(#rear-body-clip)">
        <polygon class="rear-band" fill="var(--wrap-orange)" points="140,520 546,590 546,710 140,710"/>
      </g>
      <line class="door-split" x1="343" y1="44" x2="343" y2="700" stroke="var(--trim-black)" stroke-width="2" opacity="0.7"/>
      <rect class="tail-lamp" x="160" y="470" width="16" height="92" rx="4" fill="var(--lamp-red)"/>
      <rect class="tail-lamp" x="510" y="470" width="16" height="92" rx="4" fill="var(--lamp-red)"/>
      <rect class="brake-lamp" x="306" y="34" width="74" height="8" fill="var(--lamp-red)"/>
      <rect class="bumper" x="146" y="700" width="394" height="34" rx="6" fill="var(--trim-black)"/>
      <rect x="166" y="734" width="40" height="30" rx="6" fill="var(--tyre)"/>
      <rect x="480" y="734" width="40" height="30" rx="6" fill="var(--tyre)"/>
    </g>

    <circle class="emblem-ring" cx="362" cy="236" r="160" fill="none" stroke="var(--wrap-orange)" stroke-width="8"/>

    <g transform="rotate(7 320 500)">
      <text class="wordmark" x="200" y="482" font-size="38">Bramwell</text>
      <text class="wordmark" x="198" y="520" font-size="26">Crest Electric</text>
    </g>

    <text class="contact site-url" x="200" y="588" font-size="20" transform="rotate(8 200 588)">www.bramwellcrestelectric.com</text>
    <text class="contact phone" x="356" y="672" font-size="32">555.014.2290</text>
  </svg>

</main>
</body>
</html>
```